Unique Builder wordpress website - Supply Graphics Only

We need a brand new website for a building company in Perth, Australia who constructs insulated panels (sip).
What is a SIP?
A SIP is a high-performance building panel used for floors, walls, and roofs in residential and commercial buildings. Panels are typically made using Expanded Polystyrene (EPS) sandwiched between two structural skins.
The design must incorporate a slick professional look and keep to the logo colours (Lime green & Blacks). The logo must not change colours or be altered. (
We will convert the graphics to a wordpress site. We have our own coders)
Design:
The website design must be clean, mobile friendly and the final design will be adapted to WordPress CMS.
The menus must contain dropdown menus and front page may contain a youtube video at a later date.
Fonts must be clear and easy to read
The contact us page will need to have an online form and google map.
The 16 pages listed will be the complete site and are for reference only. For this project the winning designer would need to supply the Homepage, and 1 inner pages only as PSD files.
The structure is as follows:
Home
About us
Marlow Fen Dwellings
What is a sip
Benefits
FAQ
Designs
Residential
Granny Flats
Architectural design
Photo Gallery <--- Would be great if a sample design can be provided
Services
Project management and custom design
Site Assembly
Kit Supply
Contact us
***We don't need the designer to design every page however a 1 inner page would be ideal****
Our Competitors websites
Note: the following websites look crap however, the following websites are some of our competitors. We want a clean and awesome layout.
http://www.corvamoda.com.au/
http://dralventorix.com.au/
http://www.quilbarrow.net.au/
New home builders and commercial builders
Building
5+ page

```html
<!DOCTYPE html>
<html lang="en">
<head>
<meta charset="utf-8">
<title>Brenmoor – Home</title>
<link rel="stylesheet" href="https://fonts.googleapis.com/css2?family=Exo+2:wght@400;500;600;700&family=PT+Sans:wght@400;700&display=swap">
<style>
:root{
  --lime:#8dbb2e;
  --lime-bright:#a6d13a;
  --lime-dark:#6f9a1d;
  --ink:#1e1e1e;
  --panel:#353535;
  --menu:#323232;
  --menu-active:#262626;
  --text:#3a3a3a;
  --muted:#666;
  --white:#fff;
}
*{margin:0;padding:0;box-sizing:border-box}
html,body{width:974px;height:1200px;overflow:hidden;background:var(--white)}
body{position:relative;font-family:"PT Sans",sans-serif;color:var(--text)}
.abs{position:absolute}

/* header */
.site-header{left:0;top:0;width:974px;height:92px;background:var(--white)}
.brand{left:90px;top:30px;display:flex;align-items:center;gap:10px}
.brand-mark{width:22px;height:22px;background:var(--lime)}
.brand-name{font-family:"Exo 2",sans-serif;font-weight:600;font-size:28px;color:#333;line-height:1}
.call{left:722px;top:45px;display:flex;align-items:center;gap:7px}
.call-label{font-size:8px;color:#555}
.call-number{font-size:16px;color:#333;line-height:1.1}

/* nav */
.main-nav{left:0;top:92px;width:974px;height:51px;background:linear-gradient(#2a2a2a,#151515)}
.nav-home{left:90px;top:92px;width:76px;height:51px}
.nav-item{top:111px;font-family:"Exo 2",sans-serif;font-size:10px;font-weight:500;color:var(--white);white-space:nowrap}
.nav-item.is-current{color:var(--ink);font-weight:600}
.nav-item.is-open{color:var(--lime-bright)}

/* hero */
.hero{left:0;top:143px;width:974px;height:417px;background:radial-gradient(ellipse at 50% 40%,#9cc843,#7ba928 75%)}
.slider{left:90px;top:166px;width:790px;height:372px;background:#2b2b2b}
.slide-photo{left:95px;top:172px;width:783px;height:361px;background:linear-gradient(#dfe4ea 0%,#cfd4d6 22%,#b89e6e 30%,#9b8a5e 55%,#c79a67 62%,#8d7c55 80%,#6d6148 100%)}
.slide-caption{left:95px;top:460px;width:783px;height:73px;background:rgba(30,30,30,.82)}
.slide-title{left:126px;top:484px;font-family:"Exo 2",sans-serif;font-size:24px;color:var(--white);letter-spacing:.3px}
.slide-arrow{top:487px;width:24px;height:24px}

/* dropdown */
.dropdown{left:669px;top:143px;width:259px;height:231px;background:var(--menu);box-shadow:0 3px 8px rgba(0,0,0,.3)}
.dropdown-pointer{left:717px;top:135px}
.dropdown ul{list-style:none;padding-top:9px}
.dropdown li{height:30.6px;display:flex;align-items:center;padding-left:32px;font-family:"Exo 2",sans-serif;font-size:9.4px;color:var(--white);text-transform:uppercase;gap:5px}
.dropdown li.is-active{background:var(--menu-active);color:var(--lime-bright)}
.bullet{width:9px;height:9px}

/* welcome */
.welcome-title{left:90px;top:590px;font-family:"Exo 2",sans-serif;font-size:18px;font-weight:400;color:#222;letter-spacing:.2px}
.welcome-copy{left:90px;top:624px;width:620px;font-size:9.6px;color:var(--muted);line-height:21px}
.benefit-list{left:121px;top:674px;list-style:none}
.benefit-list li{height:30.6px;display:flex;align-items:center;gap:8px;font-size:10.5px;color:#444}
.tick{width:10px;height:10px}
.video{left:633px;top:674px;width:250px;height:155px;border:3px solid #111;background:linear-gradient(90deg,#c8c4bc,#b89265 20%,#e9e9e6 45%,#f2f2f0 70%,#d6d3c4 90%,#c6c7c8)}
.video-play{left:92px;top:52px}

/* call to action */
.cta{left:0;top:869px;width:974px;height:195px;background:var(--panel);text-align:center}
.cta-title{position:absolute;left:0;width:974px;top:31px;font-size:16.6px;line-height:21px;color:var(--white)}
.cta-sub{position:absolute;left:0;width:974px;top:85px;font-size:9.2px;color:var(--white)}
.cta-button{position:absolute;left:418px;top:120px;width:138px;height:45px;border-radius:3px;background:linear-gradient(#a3cd3c,#7ba925);font-family:"Exo 2",sans-serif;font-weight:600;font-size:12px;color:#1f2a08;line-height:45px;letter-spacing:.3px}

/* footer */
.contact-bar{left:0;top:1064px;width:974px;height:69px;background:linear-gradient(#262626,#1d1d1d)}
.contact-item{top:1092px;display:flex;align-items:center;gap:6px;font-size:9.5px;color:#ddd}
.social{top:1086px;width:22px;height:22px;border-radius:50%}
.legal{left:0;top:1133px;width:974px;height:67px;background:var(--panel)}
.legal-links{left:90px;top:1160px;font-size:9.5px;color:#ccc}
.copyright{right:90px;top:1160px;font-size:9.5px;color:#ccc}
</style>
</head>
<body>

<header class="site-header abs">
  <div class="brand abs"><span class="brand-mark"></span><span class="brand-name">Brenmoor</span></div>
  <div class="call abs">
    <svg width="34" height="34" viewBox="0 0 34 34"><circle cx="17" cy="17" r="15" fill="none" stroke="#8dbb2e" stroke-width="2.5"/><path d="M11 10c1-1 2-1 3 0l2 3c.5 1 0 2-1 2.5 1 2 2.5 3.5 4.5 4.5.5-1 1.5-1.5 2.5-1l3 2c1 1 1 2 0 3-2 2-5 1.5-8-1s-5-5.5-6.5-8.5c-.7-2-.5-3.5.5-4.5z" fill="#8dbb2e"/></svg>
    <div><div class="call-label">If Any Questions? Call Now</div><div class="call-number">123 456 789 000</div></div>
  </div>
</header>

<nav class="main-nav abs"></nav>
<svg class="nav-home abs" viewBox="0 0 76 51"><path d="M0 0H76V39L38 48 0 39Z" fill="#8dbb2e"/><path d="M0 39L38 48 76 39V43L38 52 0 43Z" fill="#5f8418"/></svg>
<span class="nav-item is-current abs" style="left:115px">HOME</span>
<span class="nav-item abs" style="left:196px">ABOUT US</span>
<span class="nav-item abs" style="left:295px">WHAT IS A SIP</span>
<span class="nav-item abs" style="left:411px">BENEFITS</span>
<span class="nav-item abs" style="left:508px">FAQ</span>
<span class="nav-item abs" style="left:580px">PHOTO GALLERY</span>
<span class="nav-item is-open abs" style="left:707px">SERVICES</span>
<span class="nav-item abs" style="left:803px">CONTACT US</span>

<section class="hero abs"></section>
<div class="slider abs"></div>
<div class="slide-photo abs" role="img" aria-label="Timber wall frames with insulation panels on a building site"></div>
<div class="slide-caption abs"></div>
<div class="slide-title abs">PROJECT MANAGEMENT AND CUSTOM DESIGN</div>
<svg class="slide-arrow abs" style="left:800px" viewBox="0 0 24 24"><circle cx="12" cy="12" r="12" fill="#777"/><circle cx="12" cy="12" r="10" fill="#5a5a5a"/><path d="M14 7L8 12l6 5z" fill="#fff"/></svg>
<svg class="slide-arrow abs" style="left:831px" viewBox="0 0 24 24"><circle cx="12" cy="12" r="12" fill="#777"/><circle cx="12" cy="12" r="10" fill="#5a5a5a"/><path d="M10 7l6 5-6 5z" fill="#fff"/></svg>

<svg class="dropdown-pointer abs" width="12" height="8" viewBox="0 0 12 8"><path d="M6 0L12 8H0z" fill="#323232"/></svg>
<div class="dropdown abs">
  <ul>
    <li><svg class="bullet" viewBox="0 0 10 10"><circle cx="5" cy="5" r="5" fill="#fff"/><path d="M4 3l3 2-3 2z" fill="#323232"/></svg>Marlow Fen Dwellings</li>
    <li><svg class="bullet" viewBox="0 0 10 10"><circle cx="5" cy="5" r="5" fill="#fff"/><path d="M4 3l3 2-3 2z" fill="#323232"/></svg>Residential</li>
    <li><svg class="bullet" viewBox="0 0 10 10"><circle cx="5" cy="5" r="5" fill="#fff"/><path d="M4 3l3 2-3 2z" fill="#323232"/></svg>Granny Flats Site</li>
    <li><svg class="bullet" viewBox="0 0 10 10"><circle cx="5" cy="5" r="5" fill="#fff"/><path d="M4 3l3 2-3 2z" fill="#323232"/></svg>Assembly</li>
    <li class="is-active"><svg class="bullet" viewBox="0 0 10 10"><circle cx="5" cy="5" r="5" fill="#a6d13a"/><path d="M4 3l3 2-3 2z" fill="#262626"/></svg>Kit Supply</li>
    <li><svg class="bullet" viewBox="0 0 10 10"><circle cx="5" cy="5" r="5" fill="#fff"/><path d="M4 3l3 2-3 2z" fill="#323232"/></svg>Architectural Design</li>
    <li><svg class="bullet" viewBox="0 0 10 10"><circle cx="5" cy="5" r="5" fill="#fff"/><path d="M4 3l3 2-3 2z" fill="#323232"/></svg>Project Management and Custom Design</li>
  </ul>
</div>

<h1 class="welcome-title abs">WELCOME TO BRENMOOR</h1>
<p class="welcome-copy abs">Brenmoor are designers and manufacturers of an engineered structural insulated panel and concealed structural frame building product.<br>sips is rapidly becoming the building method of choice because of its overwhelming benefits and proven suitability.</p>
<ul class="benefit-list abs">
  <li><svg class="tick" viewBox="0 0 10 10"><circle cx="5" cy="5" r="5" fill="#8dbb2e"/><path d="M2.6 5.2l1.7 1.6 3.2-3.4" fill="none" stroke="#fff" stroke-width="1.3"/></svg>High level of captive insulation. (warm in winter cool in summer)</li>
  <li><svg class="tick" viewBox="0 0 10 10"><circle cx="5" cy="5" r="5" fill="#8dbb2e"/><path d="M2.6 5.2l1.7 1.6 3.2-3.4" fill="none" stroke="#fff" stroke-width="1.3"/></svg>Very strong, light weight and durable.</li>
  <li><svg class="tick" viewBox="0 0 10 10"><circle cx="5" cy="5" r="5" fill="#8dbb2e"/><path d="M2.6 5.2l1.7 1.6 3.2-3.4" fill="none" stroke="#fff" stroke-width="1.3"/></svg>20 + year history of performance in cyclonic locations in WA</li>
  <li><svg class="tick" viewBox="0 0 10 10"><circle cx="5" cy="5" r="5" fill="#8dbb2e"/><path d="M2.6 5.2l1.7 1.6 3.2-3.4" fill="none" stroke="#fff" stroke-width="1.3"/></svg>Reduced build time (save time save money it’s that easy)</li>
  <li><svg class="tick" viewBox="0 0 10 10"><circle cx="5" cy="5" r="5" fill="#8dbb2e"/><path d="M2.6 5.2l1.7 1.6 3.2-3.4" fill="none" stroke="#fff" stroke-width="1.3"/></svg>Energy efficient ( less energy to build and less energy to run ie lower power bills)</li>
</ul>
<div class="video abs" role="img" aria-label="Video still of a ladder beside white insulated wall panels">
  <svg class="video-play abs" width="50" height="50" viewBox="0 0 50 50"><circle cx="25" cy="25" r="23" fill="rgba(120,120,120,.55)" stroke="rgba(255,255,255,.6)" stroke-width="2"/><path d="M20 14l14 11-14 11z" fill="#fff"/></svg>
</div>

<section class="cta abs">
  <p class="cta-title">Brenmoor panels can be used in residential and commercial building and are fully compliant to<br>Australian standards.</p>
  <p class="cta-sub">We specialize in supplying on time and on budget, with high quality structural kits to builders and developers specific to their needs or requirements.</p>
  <div class="cta-button">CONTACT NOW</div>
</section>

<footer>
  <div class="contact-bar abs"></div>
  <div class="contact-item abs" style="left:90px"><svg width="8" height="11" viewBox="0 0 8 11"><path d="M4 0a4 4 0 0 1 4 4c0 3-4 7-4 7S0 7 0 4a4 4 0 0 1 4-4z" fill="#8dbb2e"/><circle cx="4" cy="4" r="1.5" fill="#222"/></svg>Level 6, Lorem Ipsm, Lorem Ipsm - 123 456</div>
  <div class="contact-item abs" style="left:307px"><svg width="11" height="11" viewBox="0 0 11 11"><rect width="11" height="11" rx="2" fill="#8dbb2e"/><path d="M3.3 2.5l1.3 1.6-.7.8c.5 1 1.2 1.7 2.2 2.2l.8-.7 1.6 1.3-.8 1c-2.5-.4-4.6-2.5-5-5z" fill="#222"/></svg>123 456 789 00</div>
  <div class="contact-item abs" style="left:416px"><svg width="13" height="12" viewBox="0 0 13 12"><rect x="0" y="3" width="13" height="9" rx="1" fill="#8dbb2e"/><rect x="3" y="0" width="7" height="4" fill="#8dbb2e"/><rect x="3" y="5" width="7" height="2" fill="#222"/><rect x="3" y="8.5" width="2" height="1.5" fill="#222"/><rect x="6" y="8.5" width="2" height="1.5" fill="#222"/></svg>123 456 789 00</div>
  <div class="contact-item abs" style="left:527px"><svg width="13" height="9" viewBox="0 0 13 9"><rect width="13" height="9" fill="#8dbb2e"/><path d="M0 0l6.5 5L13 0" fill="none" stroke="#222" stroke-width="1.2"/></svg>info@domainname.com</div>
  <div class="social abs" style="left:777px;background:#4a67a8"></div>
  <div class="social abs" style="left:805px;background:#3aa3d9"></div>
  <div class="social abs" style="left:833px;background:#2b86b4"></div>
  <div class="social abs" style="left:861px;background:#f0801d"></div>
  <div class="legal abs"></div>
  <div class="legal-links abs">Privacy Policy &nbsp;|&nbsp; Sitemap</div>
  <div class="copyright abs">Copyrights@2016 Brenmoor. All Rights Reserved.</div>
</footer>

</body>
</html>
```